BrivoTerna. Lantern of the Steady Harvest. Business card

Professional business card for BrivoTerna (Lantern of the Steady Harvest)
My rationale: Strategy-> Execution-> Results-> Value that lead to the BrivoTerna name: We put the Lantern of the Steady Harvest.
We deliver value to our customers helping them at defining a good strategy (cyan arrow). 90% of well formulated strategies fail due to poor execution so we also consider strategical execution very important (green arrow). Due to the execution we obtain the results (blue arrow). Finally, the results provide feedback to redefine strategy, and the new strategy has to be executed and new results obtained providing new feedback and on and on. It's like a wheel that finally, must create corporate value: value for shareholders, staholders, employees, providers...-

Target Market(s)

CEOs and steering comitees , invewrnent funds

Industry/Entity Type

Business Consultant

Contact Information for Business Card

Teodoro Vinsquel
CEO & Founder
teodoro.vinsquel@brivoterna-example.com
Mobile: +34 655.803.912
www.brivoterna-example.com

Colors

Designer to choose colors to be used in the design.

Requirements
Nice to have
• Nice to hace the words: Strategy, execution, results
• Nice to vave the claim: Lantern of the Steady Harvest
• The three colors should be shown:
• cyan for STRATEGY
• green for EXECUTION
• blue for RESULTS
Should not have
• Complete black background

```html
<!DOCTYPE html>
<html lang="en">
<head>
<meta charset="utf-8">
<title>BrivoTerna – Business Card</title>
<link rel="stylesheet" href="https://fonts.googleapis.com/css2?family=Arimo:wght@400;700&display=swap">
<style>
  :root {
    --navy: #1f3684;
    --navy-deep: #172a6b;
    --cyan: #1fa6dc;
    --green: #8cc43f;
    --paper: #f4f4f2;
    --ink: #2a2a2e;
    --backdrop: #e6e3dc;
  }
  * { box-sizing: border-box; margin: 0; padding: 0; }
  html, body { width: 1200px; height: 1200px; overflow: hidden; }
  body {
    background: var(--backdrop);
    font-family: "Arimo", Arial, sans-serif;
    position: relative;
  }
  .card {
    position: absolute;
    left: 160px;
    width: 880px;
    height: 500px;
    overflow: hidden;
    box-shadow: 0 10px 30px rgba(0,0,0,0.18);
  }
  .card--front { top: 70px; background: var(--paper); }
  .card--back { top: 630px; background: var(--navy); }

  .front-wave { position: absolute; inset: 0; width: 100%; height: 100%; }

  .front-brand {
    position: absolute;
    left: 60px; top: 150px;
    width: 340px;
    display: flex; align-items: center; gap: 14px;
  }
  .brand-dot {
    width: 22px; height: 22px; border-radius: 50%;
    background: var(--green); flex: none;
  }
  .brand-name {
    font-weight: 700; font-size: 52px; color: var(--navy);
    letter-spacing: -1px;
  }
  .front-divider {
    position: absolute; left: 440px; top: 70px;
    width: 2px; height: 240px; background: var(--navy);
  }
  .front-details { position: absolute; left: 470px; top: 78px; right: 20px; }
  .person-name { font-weight: 700; font-size: 34px; color: var(--navy); }
  .person-title { font-size: 19px; color: var(--ink); margin-top: 4px; }
  .contact-list { list-style: none; margin-top: 22px; }
  .contact-item {
    display: flex; align-items: center; gap: 12px;
    font-size: 17px; color: var(--ink); margin-bottom: 12px;
    white-space: nowrap;
  }
  .contact-icon { width: 20px; height: 20px; flex: none; }

  .back-brand {
    position: absolute; left: 0; right: 0; top: 150px;
    display: flex; justify-content: center; align-items: center; gap: 18px;
  }
  .back-brand .brand-name { color: #fff; font-size: 84px; }
  .back-brand .brand-dot { width: 30px; height: 30px; background: #fff; }

  .pillars {
    position: absolute; left: 0; right: 0; top: 380px; height: 86px;
    background: var(--paper);
    display: flex; align-items: center; justify-content: space-around;
    padding: 0 60px;
    font-size: 34px;
  }
  .pillar--strategy { color: var(--cyan); }
  .pillar--execution { color: var(--green); }
  .pillar--results { color: var(--navy); }
</style>
</head>
<body>

<section class="card card--front">
  <svg class="front-wave" viewBox="0 0 880 500" preserveAspectRatio="none" aria-hidden="true">
    <path d="M0,248 C300,250 440,430 880,452 L880,460 C440,440 300,262 0,262 Z" fill="var(--cyan)"/>
    <path d="M0,264 C300,266 440,442 880,462 L880,468 C440,450 300,278 0,278 Z" fill="var(--green)"/>
    <path d="M0,290 C300,292 440,462 880,478 L880,500 L0,500 Z" fill="var(--navy)"/>
  </svg>

  <div class="front-brand">
    <span class="brand-name">BrivoTerna</span>
    <span class="brand-dot"></span>
  </div>

  <div class="front-divider"></div>

  <div class="front-details">
    <h1 class="person-name">Teodoro Vinsquel</h1>
    <p class="person-title">CEO &amp; Founder</p>
    <ul class="contact-list">
      <li class="contact-item">
        <svg class="contact-icon" viewBox="0 0 24 24"><path d="M6.6 10.8a15 15 0 0 0 6.6 6.6l2.2-2.2a1 1 0 0 1 1-.25 11.4 11.4 0 0 0 3.6.57 1 1 0 0 1 1 1V20a1 1 0 0 1-1 1A17 17 0 0 1 3 4a1 1 0 0 1 1-1h3.5a1 1 0 0 1 1 1c0 1.25.2 2.45.57 3.6a1 1 0 0 1-.25 1Z" fill="var(--navy)"/></svg>
        +34 655.803.912
      </li>
      <li class="contact-item">
        <svg class="contact-icon" viewBox="0 0 24 24"><rect x="2.5" y="5" width="19" height="14" rx="1.5" fill="none" stroke="var(--navy)" stroke-width="2"/><path d="M3 6l9 7 9-7" fill="none" stroke="var(--navy)" stroke-width="2"/></svg>
        teodoro.vinsquel@brivoterna-example.com
      </li>
      <li class="contact-item">
        <svg class="contact-icon" viewBox="0 0 24 24"><circle cx="12" cy="12" r="9" fill="var(--navy)"/><path d="M3 12h18M12 3c3 3 3 15 0 18M12 3c-3 3-3 15 0 18" fill="none" stroke="var(--paper)" stroke-width="1.2"/></svg>
        www.brivoterna-example.com
      </li>
    </ul>
  </div>
</section>

<section class="card card--back">
  <div class="back-brand">
    <span class="brand-name">BrivoTerna</span>
    <span class="brand-dot"></span>
  </div>
  <div class="pillars">
    <span class="pillar pillar--strategy">Strategy</span>
    <span class="pillar pillar--execution">Execution</span>
    <span class="pillar pillar--results">Results</span>
  </div>
</section>

</body>
</html>
```